Tech business card design

We need an amazing business card design for our new business 'Pexla' a marketing tech startup based in Sydney, Australia. We provide an online marketplace for businesses to search and buy advertising media, connect with service providers and learn more about marketing. We wish to communicate 'cool tech', reliability and professionalism and design based around our logo.

Target Market(s)

Business Owners

Contact Information for Business Card

Name
Position
Email Address
Website
Phone Number

Font styles to use
Other font styles liked:
• Avenir & Avenir Next

Colors

Designer to choose colors to be used in the design.

```html
<!DOCTYPE html>
<html lang="en">
<head>
<meta charset="utf-8">
<title>Pexla Business Card</title>
<link href="https://fonts.googleapis.com/css2?family=Nunito+Sans:wght@400;700;900&display=swap" rel="stylesheet">
<style>
  :root {
    --navy: #171d48;
    --navy-deep: #12173a;
    --white: #ffffff;
    --grey-strip: #8a8a8e;
    --wordmark-light: #a4a6bd;
    --url-light: #8d90aa;
    --stage: #2a2a2c;
  }
  * { margin: 0; padding: 0; box-sizing: border-box; }
  html, body {
    width: 1200px; height: 900px; overflow: hidden;
    background: var(--stage);
    font-family: "Nunito Sans", "Avenir Next", Arial, sans-serif;
  }
  .canvas {
    position: relative; width: 1200px; height: 900px;
  }
  .card {
    position: absolute;
    width: 600px; height: 343px;
    left: 300px;
    border-radius: 24px;
    overflow: hidden;
    box-shadow: 0 14px 30px rgba(0,0,0,0.45);
  }
  /* Front */
  .card-front { top: 84px; background: var(--white); }
  .front-wordmark {
    position: absolute; left: 48px; top: 132px;
    font-weight: 900; font-size: 92px; letter-spacing: -1px;
    color: var(--navy); line-height: 1;
  }
  .url-strip {
    position: absolute; left: 362px; top: 34px;
    width: 26px; height: 276px;
    background: var(--grey-strip);
    display: flex; align-items: center; justify-content: center;
  }
  .url-strip span {
    transform: rotate(90deg);
    white-space: nowrap;
    color: var(--white); font-size: 13px; letter-spacing: 3px;
  }
  .info-panel {
    position: absolute; left: 388px; top: 34px;
    width: 212px; height: 276px;
    background: var(--navy);
    color: var(--white);
    padding: 22px 16px 0 22px;
  }
  .person-name { font-weight: 700; font-size: 17px; letter-spacing: 0.3px; line-height: 1.1; }
  .person-role { font-weight: 700; font-size: 12px; margin-top: 3px; }
  .contact-list { list-style: none; margin-top: 22px; }
  .contact-list li {
    display: flex; align-items: center; gap: 6px;
    font-size: 13px; line-height: 1; margin-bottom: 9px;
  }
  .contact-list svg { width: 12px; height: 12px; flex: none; }
  .address { font-size: 13px; line-height: 1.3; margin-top: 26px; }
  /* Back */
  .card-back {
    top: 473px; background: var(--navy-deep);
    display: flex; flex-direction: column; align-items: center; justify-content: center;
  }
  .back-wordmark {
    font-weight: 900; font-size: 150px; letter-spacing: -2px;
    color: var(--wordmark-light); line-height: 0.9;
  }
  .back-url {
    margin-top: 18px;
    font-size: 15px; letter-spacing: 4px; color: var(--url-light);
  }
</style>
</head>
<body>
<main class="canvas">
  <section class="card card-front" aria-label="Business card front">
    <div class="front-wordmark">pexla</div>
    <div class="url-strip"><span>www.pexla.com</span></div>
    <div class="info-panel">
      <div class="person-name">JOHN SMITH</div>
      <div class="person-role">Position</div>
      <ul class="contact-list">
        <li>
          <svg viewBox="0 0 12 12" aria-hidden="true"><path fill="#fff" d="M2.4 0.8l1.8 0 0.8 2.6-1.2 0.9c0.5 1.3 1.6 2.4 2.9 2.9l0.9-1.2 2.6 0.8 0 1.8c0 0.7-0.6 1.2-1.3 1.1C4.9 9.2 2.8 7.1 1.3 2.1 1.2 1.4 1.7 0.8 2.4 0.8z"/></svg>
          012-345-6789
        </li>
        <li>
          <svg viewBox="0 0 12 12" aria-hidden="true"><rect x="0.5" y="2" width="11" height="8" fill="#fff"/><path d="M0.5 2l5.5 4.5L11.5 2" fill="none" stroke="#171d48" stroke-width="1"/></svg>
          info@pexla.com
        </li>
        <li>
          <svg viewBox="0 0 12 12" aria-hidden="true"><g fill="none" stroke="#fff" stroke-width="1"><circle cx="6" cy="6" r="5"/><ellipse cx="6" cy="6" rx="2.2" ry="5"/><path d="M1 6h10"/></g></svg>
          www.pexla.com
        </li>
      </ul>
      <p class="address">Street Name, City Name<br>Zipcode:012345</p>
    </div>
  </section>

  <section class="card card-back" aria-label="Business card back">
    <div class="back-wordmark">pexla</div>
    <div class="back-url">www.pexla.com</div>
  </section>
</main>
</body>
</html>
```